Vardem Web, LLC. is the name of the company that will be an Internet startup working in E-commerce and

We are a new company and going to start the business by hiring people we need. We are on “Hiring Now…” status right now which we like to be displayed on the website homepage.
The website should allow us to start the hiring process with letting people see and apply for jobs posted on the website.

the company logo is attached.

Target Market(s)

Tech Job Seekers, Programmers, iOS and Android Developers, Software engineers, Graphic designers, QA engineers, Customer Service Reps,...

Industry/Entity Type

Internet

Number of Pages Required

5+ page

Font styles to use
Serif
Sans Serif

Colors

Designer to choose colors to be used in the design.

Requirements
Must have
• We need a system to help job seekers to upload the resume and cover letter and fill the required forms and answer some questions on a form designed to evaluate the job seekers and let them know if they fit in the position and should apply for it.
• We also want job seekers to do a Pre-Employment Tests including Aptitude, Personality, and Skills after they qualified for a job which links our website to web-based pre-employment testing services websites like (Talvexa, Plivmark, Quorvane & Associates, Dunholt Assessment, …)

```html
<!DOCTYPE html>
<html lang="en">
<head>
<meta charset="utf-8">
<title>Vardem Web — Hiring Now</title>
<link href="https://fonts.googleapis.com/css2?family=Lato:wght@400;700&family=Raleway:wght@400;500;600;700&display=swap" rel="stylesheet">
<style>
:root{
  --blue:#2b84c6;
  --blue-dark:#1f6fa9;
  --orange:#ff5a10;
  --teal:#5bc2c9;
  --grey:#7b7b7b;
  --ink:#333;
  --text:#666;
  --light:#ededed;
  --white:#fff;
}
*{box-sizing:border-box;margin:0;padding:0}
html,body{width:1200px;height:3120px;overflow:hidden}
body{font-family:'Raleway',sans-serif;color:var(--text);background:var(--white);position:relative}
section,header,footer{position:absolute;left:0;width:1200px}
.photo{position:absolute}

/* header */
.site-header{top:0;height:108px;background:var(--white);z-index:3}
.brand{position:absolute;left:78px;top:30px;display:flex;align-items:center;gap:12px;font-family:'Lato',sans-serif;font-weight:700;font-size:40px;color:var(--blue)}
.brand-dot{width:14px;height:14px;background:var(--orange)}
.nav{position:absolute;right:78px;top:0;display:flex;height:108px}
.nav a{display:block;padding:0 30px;line-height:108px;font-size:17px;color:#666;text-decoration:none;letter-spacing:.5px}
.nav a.active{background:var(--blue);color:var(--white);height:114px;padding:0 24px}

/* hero */
.hero{top:108px;height:570px;background:linear-gradient(180deg,#9a9a9a 0%,#6e6e6e 45%,#3e3e3e 100%);overflow:hidden}
.hero-person{right:260px;top:0;width:330px;height:570px;background:linear-gradient(180deg,#8a7a70,#e4e0dc 55%,#2a2a2a)}
.hiring-box{position:absolute;left:237px;top:183px;width:575px;height:256px;background:var(--blue);border:4px solid var(--orange);border-right:none;padding:40px 26px}
.hiring-box h1{font-family:'Lato',sans-serif;font-weight:700;font-size:50px;color:var(--white);line-height:1}
.hiring-box p{color:var(--white);font-size:16px;line-height:26px;margin-top:14px;width:420px}
.search{display:flex;gap:12px;margin-top:18px}
.search span{display:block;height:34px;background:var(--white);font-size:14px;font-style:italic;color:#888;padding:8px 12px}
.search .kw{width:156px}.search .cat{width:152px}
.search .go{width:84px;background:var(--orange);color:var(--white);font-style:normal;text-align:center;font-size:18px}

/* tests band */
.tests{top:716px;left:77px;width:1046px;height:206px;background:var(--orange);color:var(--white);text-align:center}
.tests h2{font-family:'Lato',sans-serif;font-weight:400;font-size:31px;margin-top:30px;display:inline-block;padding:0 16px;border-left:2px solid #fff;border-right:2px solid #fff;line-height:22px}
.tests .rule{width:48px;height:1px;background:rgba(255,255,255,.6);margin:24px auto 18px}
.tests ul{list-style:none;display:flex;justify-content:center;gap:70px}
.tests li{font-family:'Lato',sans-serif;font-weight:700;font-size:26px;padding:0 50px;border-bottom:1px solid rgba(255,255,255,.35);line-height:28px}

/* about */
.about{top:960px;height:200px;text-align:center}
.sec-title{font-family:'Lato',sans-serif;font-weight:400;font-size:41px;color:var(--blue)}
.sec-title em{font-style:normal;color:var(--orange)}
.about p{width:720px;margin:16px auto 0;font-size:14px;line-height:26px}
.pill{display:inline-block;border:2px solid var(--orange);border-radius:24px;padding:0 26px;line-height:40px;font-size:18px;color:var(--blue);background:var(--white);text-decoration:none}
.about .pill{margin-top:16px}

/* services */
.services{top:1190px;height:520px;background:var(--light);text-align:center}
.services .sec-title{margin-top:42px}
.cards{position:absolute;top:106px;left:77px;display:flex;gap:40px}
.card{width:231px;height:337px;border:2px solid #cfcfcf;background:var(--light);padding-top:24px}
.icon{width:124px;height:124px;border-radius:50%;margin:0 auto;display:flex;align-items:center;justify-content:center;border:4px solid var(--white);outline:2px solid currentColor}
.card h3{font-family:'Lato',sans-serif;font-weight:400;font-size:22px;line-height:24px;margin-top:14px;min-height:48px}
.card p{font-size:14px;line-height:22px;padding:0 22px;margin-top:2px}
.card .btn{display:inline-block;margin-top:10px;width:156px;line-height:38px;border-radius:20px;color:var(--white);font-size:18px;box-shadow:0 0 0 2px var(--white),0 0 0 4px currentColor}
.c-blue{color:var(--blue)}.c-orange{color:var(--orange)}.c-teal{color:var(--teal)}.c-grey{color:var(--grey)}
.bg-blue{background:var(--blue)}.bg-orange{background:var(--orange)}.bg-teal{background:var(--teal)}.bg-grey{background:var(--grey)}
.card .btn span{color:var(--white)}

/* career */
.career{top:1710px;height:303px}
.career .sec-title{position:absolute;left:78px;top:44px;text-align:left}
.career p{position:absolute;left:78px;top:100px;width:520px;font-size:14px;line-height:25px}
.career .actions{position:absolute;left:78px;top:210px;display:flex;gap:12px}
.career .pill{line-height:42px}
.career .pill.fill{background:#fde4d6;width:230px;text-align:center}
.team{left:645px;top:0;width:478px;height:303px;background:radial-gradient(ellipse at center,#8a7866 0%,#50565e 50%,#fff 100%)}

/* news */
.news{top:2013px;height:312px;background:var(--light);text-align:center}
.news .sec-title{margin-top:40px}
.news-item{position:absolute;top:118px;display:flex;gap:12px;text-align:left}
.thumb{width:240px;height:136px;background:linear-gradient(135deg,#c9d6e0,#6d8597)}
.news-item .date{font-size:13px;color:var(--blue);border-bottom:1px solid #bbb;padding-bottom:2px}
.news-item h4{font-size:15px;color:var(--ink);font-weight:700;line-height:22px;width:200px}
.news-item p{font-size:14px;line-height:25px;width:200px;border-top:1px solid #bbb;padding-top:4px;margin-top:4px}

/* contact */
.contact{top:2325px;height:416px;background:linear-gradient(90deg,#f6f6f6,#fbfbfb)}
.contact-photo{left:0;top:0;width:590px;height:416px;background:linear-gradient(120deg,#e9e9ea 0%,#d8d6d4 40%,#f4f4f4 100%)}
.contact-form{position:absolute;left:709px;top:19px;width:303px;height:378px;background:var(--orange);border-radius:0 0 6px 6px}
.form-head{position:relative;height:80px;background:var(--blue);color:var(--white);text-align:center;font-family:'Lato',sans-serif;font-size:33px;padding-top:10px}
.form-head svg{position:absolute;left:0;bottom:-24px}
.fields{padding:34px 19px 0}
.field{height:32px;background:#f6f6f6;margin-bottom:10px;font-size:13px;padding:8px;color:#777;border:1px solid #ddd}
.field.msg{height:82px}
.submit{display:block;width:136px;margin:4px auto 0;line-height:36px;background:var(--blue);color:var(--white);text-align:center;font-size:18px;border:2px solid #fff}

/* info */
.info{top:2741px;height:312px;background:var(--light)}
.info h2{font-family:'Lato',sans-serif;font-weight:400;font-size:31px;color:var(--orange);position:absolute;top:30px}
.divider{position:absolute;left:600px;top:30px;width:1px;height:250px;background:#ccc}
.testi{position:absolute;left:84px;display:flex;gap:24px;align-items:center}
.avatar{width:80px;height:80px;border-radius:50%;background:linear-gradient(180deg,#c7b5a8,#6d5a52);border:3px solid #fff}
.testi p{font-size:14px;line-height:22px;width:260px}
.testi b{color:var(--ink)}
.ci{position:absolute;left:722px;display:flex;gap:22px;align-items:center}
.ci-icon{width:68px;height:68px;border-radius:50%;background:var(--white);display:flex;align-items:center;justify-content:center}
.ci p{font-size:14px;line-height:26px;width:260px}

.site-footer{top:3053px;height:67px;background:var(--blue);color:var(--white);text-align:center;line-height:67px;font-size:14px}
</style>
</head>
<body>

<header class="site-header">
  <div class="brand"><span>Vardem Web</span><span class="brand-dot"></span></div>
  <nav class="nav">
    <a class="active" href="#">HOME</a><a href="#">ABOUT</a><a href="#">SERVICES</a><a href="#">CAREER</a><a href="#">NEWS</a><a href="#">CONTACT</a>
  </nav>
</header>

<section class="hero">
  <div class="photo hero-person" role="img" aria-label="Photo of a smiling recruiter holding a folder in front of a grey city skyline"></div>
  <div class="hiring-box">
    <h1>Hiring Now…</h1>
    <p>Lorem Ipsum is simply dummy text of the printing and typesetting industry.</p>
    <div class="search"><span class="kw">Keyword</span><span class="cat">-Category-</span><span class="go">GO</span></div>
  </div>
</section>

<section class="tests">
  <h2>Pre-Employment Tests</h2>
  <div class="rule"></div>
  <ul><li>Aptitude</li><li>Personality</li><li>Skills</li></ul>
</section>

<section class="about">
  <h2 class="sec-title">About <em>Vardem Web</em></h2>
  <p>Lorem Ipsum is simply dummy text of the printing and typesetting industry. Lorem Ipsum has been the industry's standard dummy text ever since the 1500s, when an unknown printer took a galley of type and scrambled it to make a type specimen book.</p>
  <a class="pill" href="#">READ MORE</a>
</section>

<section class="services">
  <h2 class="sec-title">Our <em>Services</em></h2>
  <div class="cards">
    <div class="card c-blue">
      <div class="icon bg-blue"><svg width="60" height="60" viewBox="0 0 60 60" fill="none" stroke="#fff" stroke-width="3"><rect x="19" y="8" width="22" height="44" rx="4"/><line x1="26" y1="45" x2="34" y2="45"/></svg></div>
      <h3>Ios and Android Development</h3>
      <p>Lorem Ipsum is simply dummy text of the printing.</p>
      <span class="btn bg-blue">READ MORE</span>
    </div>
    <div class="card c-orange">
      <div class="icon bg-orange"><svg width="64" height="60" viewBox="0 0 64 60" fill="none" stroke="#fff" stroke-width="3"><rect x="6" y="8" width="52" height="34" rx="2"/><line x1="32" y1="42" x2="32" y2="52"/><line x1="20" y1="52" x2="44" y2="52"/><polyline points="24,19 18,25 24,31"/><polyline points="40,19 46,25 40,31"/><line x1="35" y1="17" x2="29" y2="33"/></svg></div>
      <h3>Software Development</h3>
      <p>Lorem Ipsum is simply dummy text of the printing.</p>
      <span class="btn bg-orange">READ MORE</span>
    </div>
    <div class="card c-teal">
      <div class="icon bg-teal"><svg width="64" height="60" viewBox="0 0 64 60" fill="none" stroke="#fff" stroke-width="3"><rect x="6" y="10" width="52" height="32" rx="2"/><line x1="32" y1="42" x2="32" y2="52"/><line x1="22" y1="52" x2="42" y2="52"/><line x1="24" y1="34" x2="44" y2="14"/></svg></div>
      <h3>Web design</h3>
      <p>Lorem Ipsum is simply dummy text of the printing and typesetting industry.</p>
      <span class="btn bg-teal">READ MORE</span>
    </div>
    <div class="card c-grey">
      <div class="icon bg-grey"><svg width="64" height="60" viewBox="0 0 64 60" fill="none" stroke="#fff" stroke-width="3"><polyline points="4,22 16,16 30,24 40,20 60,26"/><polyline points="16,30 28,40 34,38 44,30"/><line x1="4" y1="22" x2="16" y2="30"/><line x1="60" y1="26" x2="44" y2="30"/></svg></div>
      <h3>Custom Service</h3>
      <p>Lorem Ipsum is simply dummy text of the printing and typesetting industry.</p>
      <span class="btn bg-grey">READ MORE</span>
    </div>
  </div>
</section>

<section class="career">
  <h2 class="sec-title">Career</h2>
  <p>Lorem Ipsum is simply dummy text of the printing and typesetting industry. Lorem Ipsum has been the industry's standard dummy text ever since the 1500s, when an unknown printer took a galley of type and scrambled it to make a type specimen book.</p>
  <div class="actions"><a class="pill fill" href="#">upload resume</a><a class="pill" href="#">Pre-Employment Tests</a></div>
  <div class="photo team" role="img" aria-label="Photo of a cheerful group of young professionals giving thumbs up"></div>
</section>

<section class="news">
  <h2 class="sec-title">Latest <em>News</em></h2>
  <article class="news-item" style="left:102px">
    <div class="thumb" role="img" aria-label="Photo of two businessmen shaking hands in an office"></div>
    <div><div class="date">March 29, 2017</div><h4>Lorem Ipsum is simply dummy text</h4><p>Lorem Ipsum is simply dummy text of the printing and typesetting industry.</p></div>
  </article>
  <article class="news-item" style="left:638px">
    <div class="thumb" role="img" aria-label="Photo of a person working at a laptop with documents"></div>
    <div><div class="date">March 29, 2017</div><h4>Lorem Ipsum is simply dummy text</h4><p>Lorem Ipsum is simply dummy text of the printing and typesetting industry.</p></div>
  </article>
</section>

<section class="contact">
  <div class="photo contact-photo" role="img" aria-label="Photo of a man in a white shirt adjusting his black tie"></div>
  <form class="contact-form">
    <div class="form-head">Contact Us
      <svg width="303" height="24" viewBox="0 0 303 24"><polygon points="0,0 303,0 151.5,24" fill="#2b84c6"/></svg>
    </div>
    <div class="fields">
      <div class="field">Enter Name</div>
      <div class="field">Enter Email</div>
      <div class="field">Enter Contact No.</div>
      <div class="field msg">Enter Message</div>
      <span class="submit">SUBMIT</span>
    </div>
  </form>
</section>

<section class="info">
  <h2 style="left:80px">Testimonials</h2>
  <div class="testi" style="top:100px"><div class="avatar" role="img" aria-label="Client portrait"></div><p>There are many variations of passages of Lorem Ipsum available.<br><b>-Client Name</b></p></div>
  <div class="testi" style="top:202px"><div class="avatar" role="img" aria-label="Client portrait"></div><p>There are many variations of passages of Lorem Ipsum available.<br><b>-Client Name</b></p></div>
  <div class="divider"></div>
  <h2 style="left:736px">Contact info</h2>
  <div class="ci" style="top:102px">
    <div class="ci-icon"><svg width="30" height="34" viewBox="0 0 30 34" fill="none" stroke="#ff5a10" stroke-width="3"><line x1="15" y1="2" x2="15" y2="32"/><polyline points="4,8 24,8 28,12 24,16 4,16" fill="#ff5a10"/><polyline points="26,20 6,20 2,24 6,28 26,28" fill="#ff5a10"/></svg></div>
    <p>Lorem Ipsum is simply dummy text of the printing.</p>
  </div>
  <div class="ci" style="top:200px">
    <div class="ci-icon"><svg width="30" height="30" viewBox="0 0 24 24"><path fill="#ff5a10" d="M6.6 10.8a15.1 15.1 0 0 0 6.6 6.6l2.2-2.2c.3-.3.7-.4 1-.2 1.1.4 2.3.6 3.6.6.6 0 1 .4 1 1V20c0 .6-.4 1-1 1A17 17 0 0 1 3 4c0-.6.4-1 1-1h3.5c.6 0 1 .4 1 1 0 1.3.2 2.5.6 3.6.1.3 0 .7-.2 1z"/></svg></div>
    <p>Phone No. : (555) 014-2290<br>Email : hello@vardemweb.example</p>
  </div>
</section>

<footer class="site-footer">©Vardem Web. 2017 - All Rights Reserved.</footer>

</body>
</html>
```